BOLD & MINIMALIST DESIGN NEEDED

We want a very bold but minimalistic business card design that is impactful and utilizes both sides of the business card. Our current logo is included for your use.

We want bold fonts and good use of negative space. We don't want the logo to overpower the design.

Target Market(s)

Professionals who are building new commercial buildings.

Industry/Entity Type

Construction

Contact Information for Business Card

Name, Title, email, office phone, cell phone, website

Font styles to use
Serif
Sans Serif

Requirements
Must have
• Bold design!

```html
<!DOCTYPE html>
<html lang="en">
<head>
<meta charset="utf-8">
<title>Ridgeline business card</title>
<link rel="stylesheet" href="https://fonts.googleapis.com/css2?family=Montserrat:wght@400;500;800&display=swap">
<style>
  :root {
    --stage: #474747;
    --paper: #f4f4f2;
    --ink: #0c0c0c;
    --card-black: #0e0e0e;
    --emboss: #262626;
    --lime: #6fbf2a;
    --lime-deep: #5aa31e;
  }
  * { margin: 0; padding: 0; box-sizing: border-box; }
  html, body {
    width: 1200px; height: 1050px; overflow: hidden;
    background: var(--stage);
    font-family: "Montserrat", Arial, sans-serif;
  }
  .canvas { position: relative; width: 1200px; height: 1050px; }

  .card {
    position: absolute; left: 280px; width: 640px; height: 366px;
    overflow: hidden;
  }
  .card--front { top: 110px; background: var(--paper); color: var(--ink); }
  .card--back { top: 570px; background: var(--card-black); }

  .brand {
    position: absolute; display: flex; align-items: center; gap: 12px;
    font-weight: 800; letter-spacing: 0.02em; line-height: 1;
  }
  .brand__mark { display: block; background: var(--lime); }
  .card--front .brand { left: 40px; top: 38px; font-size: 34px; }
  .card--front .brand__mark { width: 22px; height: 22px; }

  .feature-block {
    position: absolute; left: 40px; bottom: 0; width: 150px; height: 150px;
    background: var(--lime);
  }

  .contact {
    position: absolute; left: 360px; top: 340px; width: 310px;
    transform: rotate(-90deg); transform-origin: top left;
  }
  .contact__name { font-size: 30px; font-weight: 800; letter-spacing: 0.01em; line-height: 1.05; }
  .contact__role { font-size: 14px; font-weight: 500; margin-bottom: 16px; }
  .contact__address { font-size: 14px; line-height: 1.35; margin-bottom: 12px; }
  .contact__list { list-style: none; font-size: 14px; line-height: 1.55; }
  .contact__list li { display: flex; align-items: center; gap: 8px; }
  .contact__icon { width: 11px; height: 11px; flex: none; }

  .card--back .brand {
    left: 50%; top: 50%; transform: translate(-50%, -50%);
    font-size: 58px; color: var(--emboss);
  }
  .card--back .brand__mark { width: 36px; height: 36px; }
</style>
</head>
<body>
<main class="canvas">
  <section class="card card--front" aria-label="Card front">
    <div class="brand"><span class="brand__mark"></span>RIDGELINE</div>
    <div class="feature-block" role="img" aria-label="Large brand symbol area in lime green"></div>
    <div class="contact">
      <p class="contact__name">MAREK OLSEN</p>
      <p class="contact__role">Director</p>
      <p class="contact__address">Birkenallee 14,<br>30171 Hannover</p>
      <ul class="contact__list">
        <li>
          <svg class="contact__icon" viewBox="0 0 12 12"><path d="M2 1l2 0 1 3-1.5 1a6 6 0 0 0 3.5 3.5L8 7l3 1v2a1 1 0 0 1-1 1A9 9 0 0 1 1 2a1 1 0 0 1 1-1z" fill="var(--lime-deep)"/></svg>
          0160 2224471
        </li>
        <li>
          <svg class="contact__icon" viewBox="0 0 12 12"><rect x="0.5" y="2" width="11" height="8" fill="var(--lime-deep)"/><path d="M0.5 2l5.5 4.5L11.5 2" fill="none" stroke="var(--paper)" stroke-width="1"/></svg>
          info@ridgeline-build.com
        </li>
        <li>
          <svg class="contact__icon" viewBox="0 0 12 12"><circle cx="6" cy="6" r="5.3" fill="none" stroke="var(--lime-deep)" stroke-width="1.2"/><path d="M0.7 6h10.6M6 0.7c-3 3-3 7.6 0 10.6M6 0.7c3 3 3 7.6 0 10.6" fill="none" stroke="var(--lime-deep)" stroke-width="1"/></svg>
          www.ridgeline-build.com
        </li>
      </ul>
    </div>
  </section>

  <section class="card card--back" aria-label="Card back">
    <div class="brand"><span class="brand__mark"></span>RIDGELINE</div>
  </section>
</main>
</body>
</html>
```